Business Card Design Project

Business Card
We are rebranding with a new logo
Industry/Entity Type
Business
Contact Information for Business Card
Dennis Morvale +61 487215963 dennis@quorv.com.au P.O. Box 872 Fernlow QLD 4309
Requirements
Must have
- Logo

```html
<!DOCTYPE html>
<html lang="en">
<head>
<meta charset="utf-8">
<title>Quorv Business Card</title>
<link href="https://fonts.googleapis.com/css2?family=Lato:wght@400;700;900&display=swap" rel="stylesheet">
<style>
  :root {
    --backdrop: #3b3b3d;
    --card: #ffffff;
    --band: #8cc4ea;
    --ink: #151515;
    --rule: #8a8a8a;
    --brand: #1b8cc8;
    --accent: #f07d1a;
  }
  * { margin: 0; padding: 0; box-sizing: border-box; }
  html, body {
    width: 1200px;
    height: 926px;
    overflow: hidden;
    background: var(--backdrop);
    font-family: "Lato", sans-serif;
  }
  .business-card {
    position: absolute;
    left: 150px;
    top: 206px;
    width: 900px;
    height: 514px;
    background: var(--card);
    box-shadow: 0 10px 30px rgba(0,0,0,0.35);
  }
  .stripe-band {
    position: absolute;
    left: 0;
    top: 216px;
    width: 423px;
  }
  .stripe-band .stripe {
    height: 26px;
    background: var(--band);
    margin-bottom: 5px;
  }
  .brand {
    position: absolute;
    left: 0;
    right: 0;
    top: 128px;
    display: flex;
    justify-content: center;
    align-items: center;
    gap: 14px;
    padding-left: 250px;
  }
  .brand-dot {
    width: 30px;
    height: 30px;
    border-radius: 50%;
    background: var(--accent);
  }
  .brand-name {
    font-size: 56px;
    font-weight: 700;
    color: var(--brand);
    letter-spacing: 1px;
  }
  .contact {
    position: absolute;
    left: 436px;
    top: 272px;
    width: 392px;
    color: var(--ink);
  }
  .contact-name {
    font-size: 29px;
    font-weight: 400;
    line-height: 38px;
  }
  .contact-name .first { font-weight: 900; }
  .contact-row {
    font-size: 21px;
    letter-spacing: 0.6px;
    line-height: 32px;
    border-bottom: 1.5px solid var(--rule);
    padding-top: 2px;
  }
</style>
</head>
<body>
  <div class="business-card">
    <div class="stripe-band" aria-hidden="true">
      <div class="stripe"></div>
      <div class="stripe"></div>
      <div class="stripe"></div>
      <div class="stripe"></div>
    </div>

    <div class="brand">
      <span class="brand-dot" aria-hidden="true"></span>
      <span class="brand-name">Quorv</span>
    </div>

    <div class="contact">
      <p class="contact-name"><span class="first">Dennis</span> Morvale</p>
      <p class="contact-row">+61 487215963</p>
      <p class="contact-row">dennis@quorv.com.au</p>
      <p class="contact-row">P.O. Box 872 Fernlow QLD 4309</p>
    </div>
  </div>
</body>
</html>
```